Business Card Design Project

This is the first time we use our new logo. We need a business card that we can use both on our institutional corporate relationships and also that works for our staff that deals with consumers directly.

VELUNDA is a new company dedicated to empower consumers and to provide them with the best choices for specialized health care using the latest telemedicine technology (medicine at a distance via videoconference).

We want to print this cards in high quality materials and process. We will like designs that allow us to use UV spot varnish and other techniques that will differentiate us.

We are including Two different versions of Color logos. In addition we are including white over black background logos. Those can be used replacing the black for a color.

Please note this is the first time we will be creating any corporate materials with our new logo and colors.

Target Market(s)

34+ consumers of medium high and high socioeconomic levels.

Industry/Entity Type

Health

Requirements
Must have
• Our logo on its original colors
Should not have
• Any other graphical element or design that is not our logo

```html
<!DOCTYPE html>
<html lang="en">
<head>
<meta charset="utf-8">
<title>VELUNDA Business Card</title>
<link rel="stylesheet" href="https://fonts.googleapis.com/css2?family=Arimo:wght@400;700&display=swap">
<style>
  :root {
    --navy: #1b4f7a;
    --teal: #00a89c;
    --sky: #5ab4e0;
    --white: #ffffff;
    --ink: #333a40;
    --rule: #c9ced3;
    --backdrop: #e9e6e1;
  }
  * { box-sizing: border-box; margin: 0; padding: 0; }
  html, body { width: 1200px; height: 1057px; overflow: hidden; }
  body {
    background: var(--backdrop);
    font-family: "Arimo", Arial, sans-serif;
    position: relative;
  }
  .card {
    position: absolute;
    left: 190px;
    width: 820px;
    height: 468px;
    overflow: hidden;
    box-shadow: 0 6px 18px rgba(0,0,0,0.18);
  }
  .card--front { top: 40px; background: var(--white); }
  .card--back { top: 549px; background: var(--teal); }

  .front-bands { position: absolute; inset: 0; }

  .brand {
    position: absolute;
    left: 50px;
    top: 205px;
    display: flex;
    align-items: center;
    gap: 16px;
  }
  .brand__dot {
    width: 34px; height: 34px;
    border-radius: 50%;
    background: var(--teal);
  }
  .brand__name {
    font-weight: 700;
    font-size: 58px;
    letter-spacing: 3px;
    color: var(--navy);
  }
  .divider {
    position: absolute;
    left: 420px; top: 60px;
    width: 1px; height: 280px;
    background: var(--rule);
  }
  .contact {
    position: absolute;
    left: 455px; top: 70px;
    color: var(--ink);
  }
  .contact__name { font-weight: 700; font-size: 34px; color: var(--navy); }
  .contact__title { font-size: 22px; color: var(--teal); margin-top: 2px; }
  .contact__list { list-style: none; margin-top: 22px; }
  .contact__list li {
    display: flex; align-items: center; gap: 10px;
    font-size: 17px; line-height: 28px;
  }
  .contact__list svg { width: 16px; height: 16px; flex: none; }
  .contact__address { margin-top: 18px; font-size: 17px; line-height: 24px; }
  .front-web {
    position: absolute;
    right: 36px; bottom: 32px;
    color: var(--white);
    font-size: 17px;
    letter-spacing: 4px;
  }

  .back-brand {
    position: absolute;
    left: 0; right: 0; top: 150px;
    display: flex; justify-content: center; align-items: center; gap: 22px;
  }
  .back-brand__dot {
    width: 52px; height: 52px; border-radius: 50%;
    background: var(--white);
  }
  .back-brand__name {
    font-weight: 700; font-size: 84px; letter-spacing: 5px;
    color: var(--white);
  }
  .back-web {
    position: absolute;
    left: 0; right: 0; bottom: 80px;
    text-align: center;
    color: var(--white);
    font-size: 26px;
    letter-spacing: 6px;
  }
</style>
</head>
<body>
  <section class="card card--front">
    <svg class="front-bands" viewBox="0 0 820 468" aria-hidden="true">
      <polygon points="0,450 520,450 565,382 590,382 540,468 0,468" fill="var(--sky)"/>
      <polygon points="590,382 820,382 820,468 540,468" fill="var(--navy)"/>
    </svg>
    <div class="brand">
      <span class="brand__dot"></span>
      <span class="brand__name">VELUNDA</span>
    </div>
    <div class="divider"></div>
    <div class="contact">
      <div class="contact__name">Your Name</div>
      <div class="contact__title">Title</div>
      <ul class="contact__list">
        <li>
          <svg viewBox="0 0 16 16"><circle cx="8" cy="8" r="7" fill="none" stroke="var(--navy)" stroke-width="1.5"/><path d="M6 4.5 L7.5 6.5 L6.8 7.5 Q7.5 9 8.8 9.6 L9.8 8.8 L11.5 10.3 Q10.5 12 9 11.6 Q5.2 10.5 4.4 6.6 Q4.4 5 6 4.5Z" fill="var(--navy)"/></svg>
          010-555-0142
        </li>
        <li>
          <svg viewBox="0 0 16 16"><circle cx="8" cy="8" r="7" fill="none" stroke="var(--navy)" stroke-width="1.5"/><path d="M6 4.5 L7.5 6.5 L6.8 7.5 Q7.5 9 8.8 9.6 L9.8 8.8 L11.5 10.3 Q10.5 12 9 11.6 Q5.2 10.5 4.4 6.6 Q4.4 5 6 4.5Z" fill="var(--navy)"/></svg>
          010-555-0142
        </li>
        <li>
          <svg viewBox="0 0 16 16"><rect x="1" y="4" width="14" height="9" rx="1" fill="var(--navy)"/><path d="M1.5 4.5 L8 9.5 L14.5 4.5" fill="none" stroke="var(--white)" stroke-width="1.2"/></svg>
          name@velunda.com
        </li>
      </ul>
      <p class="contact__address">Street Name, City Name<br>State, City Zip Code</p>
    </div>
    <div class="front-web">www.velunda.com</div>
  </section>

  <section class="card card--back">
    <div class="back-brand">
      <span class="back-brand__dot"></span>
      <span class="back-brand__name">VELUNDA</span>
    </div>
    <div class="back-web">www.velunda.com</div>
  </section>
</body>
</html>
```